Personal training and nutrition business needs business card design

We need a business card that outlays our services and invites potential customers to join our team and take the first step to a healthier and more enjoyable life. We cater for any level of fitness and specialize in weight loss and conditioning, strength training, muscle gain and strength endurance. Whether you are just starting off or need some help getting to the next level of your journey we are here to get the job done.
We specialize in one on one or one on two personal training sessions and each program will be custom made to suit individual fitness goals of our clients

```html
<!DOCTYPE html>
<html lang="en">
<head>
<meta charset="utf-8">
<title>Stride &amp; Rise – Business Card</title>
<link rel="stylesheet" href="https://fonts.googleapis.com/css2?family=Lato:wght@400;700;900&family=Arimo:wght@400&family=Bebas+Neue&family=Oswald:wght@500&display=swap">
<style>
  :root {
    --page-bg: #1d1d1f;
    --card-white: #ffffff;
    --purple: #7a4a9e;
    --purple-name: #8b52a8;
    --purple-light: #b062a8;
    --purple-dark: #7f4f9f;
    --accent-pink: #d35fb4;
    --ink: #1a1a1a;
    --rule: #cfcfcf;
    --bar-black: #070707;
  }
  * { box-sizing: border-box; margin: 0; padding: 0; }
  html, body {
    width: 1093px; height: 1200px; overflow: hidden;
    background: var(--page-bg);
  }
  .canvas { position: relative; width: 1093px; height: 1200px; }

  .card {
    position: absolute; left: 258px; width: 580px; height: 357px;
    overflow: hidden;
  }

  /* Front */
  .card-front { top: 226px; background: var(--card-white); }
  .brand {
    position: absolute; right: 40px; top: 78px;
    display: flex; flex-direction: column; align-items: flex-start;
  }
  .brand-row { display: flex; align-items: center; gap: 12px; }
  .brand-mark { width: 34px; height: 34px; background: var(--purple); }
  .brand-name {
    font-family: 'Lato', sans-serif; font-weight: 900;
    font-size: 34px; line-height: 1; letter-spacing: 0.5px;
    text-transform: uppercase;
  }
  .card-front .brand-name { color: var(--ink); }
  .brand-tagline {
    font-family: 'Oswald', sans-serif; font-weight: 500;
    font-size: 8px; letter-spacing: 0.8px; text-transform: uppercase;
    margin-top: 10px;
  }
  .card-front .brand-tagline { color: var(--purple-name); margin-left: 46px; }

  .person { position: absolute; left: 39px; top: 188px; }
  .person-name {
    font-family: 'Lato', sans-serif; font-weight: 700;
    font-size: 24px; line-height: 1; color: var(--purple-name);
    letter-spacing: -0.3px;
  }
  .person-role {
    font-family: 'Arimo', sans-serif; font-size: 16px;
    color: var(--ink); margin-top: 4px;
  }
  .role-rule {
    position: absolute; left: 187px; top: 224px; width: 350px; height: 1px;
    background: var(--rule);
  }

  .contact-list {
    position: absolute; left: 39px; top: 262px; list-style: none;
    font-family: 'Arimo', sans-serif; font-size: 16px; color: var(--ink);
  }
  .contact-list li { display: flex; align-items: center; height: 21px; }
  .contact-list svg { width: 15px; height: 15px; margin-right: 6px; fill: var(--purple); }
  .contact-list .highlight { color: var(--purple-name); }

  .address {
    position: absolute; right: 34px; top: 283px; text-align: right;
    font-family: 'Arimo', sans-serif; font-size: 16px; color: var(--ink);
    line-height: 21px;
  }
  .base-band {
    position: absolute; left: 0; bottom: 0; width: 100%; height: 11px;
    background: var(--purple);
  }

  /* Back */
  .card-back {
    top: 620px;
    background: linear-gradient(180deg, var(--purple-light) 0%, var(--purple-dark) 100%);
  }
  .back-brand {
    position: absolute; left: 0; right: 0; top: 92px;
    display: flex; flex-direction: column; align-items: center;
  }
  .back-brand .brand-mark { width: 60px; height: 60px; background: var(--card-white); margin-bottom: 26px; }
  .back-brand .brand-name { color: var(--card-white); font-size: 40px; }
  .back-brand .brand-tagline { color: var(--card-white); font-size: 9px; margin-top: 12px; }

  .services-bar {
    position: absolute; left: 0; top: 295px; width: 100%; height: 38px;
    background: var(--bar-black);
    display: flex; align-items: center; justify-content: center; gap: 9px;
    font-family: 'Bebas Neue', sans-serif; font-size: 20px;
    color: var(--card-white); letter-spacing: 0.1px; line-height: 1;
    padding-top: 2px;
  }
  .services-bar .divider { color: var(--accent-pink); }
  .card-back .base-band { height: 24px; }
</style>
</head>
<body>
<main class="canvas">

  <section class="card card-front" aria-label="Business card front">
    <div class="brand">
      <div class="brand-row">
        <span class="brand-mark"></span>
        <span class="brand-name">Stride &amp; Rise</span>
      </div>
      <span class="brand-tagline">Personal Training. Nutrition. Motivation</span>
    </div>

    <div class="person">
      <h1 class="person-name">DANIEL REYES</h1>
      <p class="person-role">Managing Director</p>
    </div>
    <div class="role-rule"></div>

    <ul class="contact-list">
      <li>
        <svg viewBox="0 0 24 24" aria-hidden="true"><path d="M6.6 10.8a15.1 15.1 0 0 0 6.6 6.6l2.2-2.2a1 1 0 0 1 1-.25 11.4 11.4 0 0 0 3.6.57 1 1 0 0 1 1 1V20a1 1 0 0 1-1 1A17 17 0 0 1 3 4a1 1 0 0 1 1-1h3.5a1 1 0 0 1 1 1c0 1.25.2 2.45.57 3.57a1 1 0 0 1-.25 1z"/></svg>
        055-210 348 617
      </li>
      <li>
        <svg viewBox="0 0 24 24" aria-hidden="true"><path d="M2 5h20v14H2z M3.5 6.5 12 13l8.5-6.5" fill="var(--purple)" stroke="#fff" stroke-width="1.4"/></svg>
        hello@strideandrise.co
      </li>
      <li>
        <svg viewBox="0 0 24 24" aria-hidden="true"><circle cx="12" cy="12" r="9.5" fill="none" stroke="var(--purple)" stroke-width="1.8"/><path d="M2.5 12h19M12 2.5c3 3 3 16 0 19M12 2.5c-3 3-3 16 0 19M4 7.5h16M4 16.5h16" fill="none" stroke="var(--purple)" stroke-width="1.4"/></svg>
        <span>www.<span class="highlight">strideandrise</span>.co</span>
      </li>
    </ul>

    <p class="address">18, Harbour Lane, Unit 4<br>30817, Eastmoor</p>
    <div class="base-band"></div>
  </section>

  <section class="card card-back" aria-label="Business card back">
    <div class="back-brand">
      <span class="brand-mark"></span>
      <span class="brand-name">Stride &amp; Rise</span>
      <span class="brand-tagline">Personal Training. Nutrition. Motivation</span>
    </div>
    <div class="services-bar">
      <span>Weight Loss &amp; Conditioning</span>
      <span class="divider">|</span>
      <span>Strength Training</span>
      <span class="divider">|</span>
      <span>Muscle Gain</span>
      <span class="divider">|</span>
      <span>Strength Endurance</span>
    </div>
    <div class="base-band"></div>
  </section>

</main>
</body>
</html>
```